Quillfern Vaults - Direct Mailer / Flyer

We are excited to announce the launch of our new company, Quillfern Vaults, a premier cohosting facility and data center dedicated to Cryptocurrency Miners. Our website, https://quillfernvaults.example, provides detailed information about our offerings and showcases the innovative design schemes for the entire project.

Quillfern Vaults stands out in the industry by offering both GPU Hosting and ASIC Hosting services in our state-of-the-art facility, equipped with an impressive 17 Megawatts of available power. What sets us apart is our unique billing system based on actual metered power usage. We charge $0.08 for ASIC miners and $0.09 for GPU miners, ensuring cost-effectiveness and transparency for our clients.

Our commitment to excellence is evident in our use of cutting-edge technology, top-notch facilities, and strategic partnerships. These elements come together to deliver exceptional solutions tailored for real-world applications in the cryptocurrency space.

As part of our promotional efforts, we are developing a direct mailer/flyer to introduce Quillfern Vaults to a wider audience. This promotional material will also serve as a handout at events, to potential customers, and more. We welcome creative ideas and suggestions to maximize the versatility of this design and reach diverse target audiences effectively.

For a comprehensive overview of our services and to explore our design concepts, please visit https://quillfernvaults.example. Quillfern Vaults is poised to revolutionize the mining industry, and we look forward to partnering with you for success in the digital currency era.

```html
<!DOCTYPE html>
<html lang="en">
<head>
<meta charset="utf-8">
<title>Quillfern Vaults – Flyer</title>
<link href="https://fonts.googleapis.com/css2?family=Poppins:wght@400;500;600;700;800;900&display=swap" rel="stylesheet">
<style>
  :root{
    --blue:#3a4ef5;
    --ink:#1f1f1f;
    --band:#3b3b3b;
    --card-grey:#5b5a59;
    --card-dark:#2e2e2e;
    --card-body:#e3e3e3;
    --rule:#c9c9c9;
    --page-bg:#efefef;
    --white:#ffffff;
    --black:#050505;
  }
  *{box-sizing:border-box;margin:0;padding:0}
  html,body{width:783px;height:1200px;overflow:hidden;background:var(--page-bg);font-family:"Poppins",sans-serif;color:var(--ink)}
  .stage{position:relative;width:783px;height:1200px}
  .flyer{position:absolute;left:0;top:93px;width:845px;height:1093px;background:var(--white);
    transform:scale(0.9266);transform-origin:0 0;overflow:hidden;box-shadow:0 2px 10px rgba(0,0,0,.12)}
  .abs{position:absolute}

  .brand{left:53px;top:52px;display:flex;align-items:center;gap:12px}
  .brand-mark{width:20px;height:20px;background:var(--ink)}
  .brand-name{font-weight:800;font-size:29px;letter-spacing:.5px;text-transform:uppercase;color:var(--ink);line-height:1}

  .headline{left:50px;top:102px;line-height:1;font-weight:800}
  .headline .l1{display:block;font-size:56px;color:var(--blue);letter-spacing:.5px}
  .headline .l2{display:block;font-size:92px;color:var(--blue);margin-top:-6px;letter-spacing:-1px}
  .headline .l3{display:block;font-size:39px;font-weight:700;color:var(--ink);margin-top:-2px}
  .rule{left:52px;top:288px;width:376px;height:1px;background:var(--rule)}
  .subhead{left:52px;top:298px;font-size:23px;font-weight:500;line-height:26px;color:var(--ink)}

  .hero{left:420px;top:20px}

  .intro-band{left:0;top:392px;width:660px;height:89px;background:var(--band);color:var(--white);
    font-size:12.6px;line-height:15px;padding:16px 80px 0 52px}
  .price-band{left:0;top:481px;width:660px;height:59px;background:var(--blue);color:var(--white);
    font-size:16.5px;font-weight:700;line-height:19px;padding:10px 40px 0 52px}

  .section-title{left:52px;top:551px;font-size:19px;font-weight:700;color:var(--blue);letter-spacing:.1px}

  .service{top:603px;width:172px;height:161px;border-radius:10px;overflow:visible;background:var(--card-body)}
  .service-head{height:60px;border-radius:10px 10px 0 0;color:var(--white);font-size:12px;font-weight:700;
    text-align:center;padding-top:38px;text-transform:uppercase}
  .service.grey .service-head{background:var(--card-grey)}
  .service.dark .service-head{background:var(--card-dark)}
  .service-icon{position:absolute;left:65px;top:-14px;width:42px;height:42px;border-radius:50%;background:var(--white);
    border:3px solid var(--blue);display:flex;align-items:center;justify-content:center}
  .service-body{font-size:13px;line-height:15px;text-align:center;padding:8px 14px 0;color:var(--ink)}

  .commit{left:52px;top:803px;width:321px;height:169px;border:1.5px dashed #555;border-top:none}
  .commit-top{left:300px;top:803px;width:73px;border-top:1.5px dashed #555}
  .commit-heading{left:51px;top:782px;background:var(--white);padding-right:14px;font-size:16px;font-weight:700;
    color:var(--blue);line-height:18px}
  .commit-list{left:73px;top:828px;list-style:none;font-size:16px;font-weight:500;line-height:22.5px}
  .commit-list li{display:flex;align-items:center;gap:6px}
  .commit-note{left:73px;top:905px;width:290px;font-size:13px;line-height:15px}

  .photo{top:792px;width:180px;height:177px;border-radius:10px;border:3px solid var(--white);box-shadow:0 2px 8px rgba(0,0,0,.25)}
  .photo.coins{left:401px;background:radial-gradient(circle at 50% 55%,#8a7f70 0%,#5a4d40 45%,#2d2620 100%)}
  .photo.trade{left:606px;background:linear-gradient(135deg,#d9ecfb 0%,#6fa6de 50%,#2a5da8 100%)}

  .footer{left:0;top:998px}
  .contact{top:1031px;font-size:15px;color:var(--white);display:flex;align-items:center;gap:7px;white-space:nowrap}
  .web{left:520px;top:1031px;font-size:15px;letter-spacing:1px;color:var(--ink);display:flex;align-items:center;gap:5px;white-space:nowrap}
  .web b{color:var(--blue);font-weight:700}
</style>
</head>
<body>
<div class="stage">
  <article class="flyer">
    <div class="abs brand"><span class="brand-mark"></span><span class="brand-name">Quillfern Vaults</span></div>

    <h1 class="abs headline"><span class="l1">TRANSFORM</span><span class="l2">MINING</span><span class="l3">WITH COHOSTING</span></h1>
    <div class="abs rule"></div>
    <p class="abs subhead">A premier cohosting facility<br>and data center dedicated to<br>Cryptocurrency Miners.</p>

    <svg class="abs hero" width="425" height="530" viewBox="0 0 425 530">
      <defs>
        <radialGradient id="rocks" cx="55%" cy="50%" r="60%">
          <stop offset="0" stop-color="#b7a99a"/>
          <stop offset=".6" stop-color="#8c8479"/>
          <stop offset="1" stop-color="#5e5a55"/>
        </radialGradient>
      </defs>
      <path d="M202 0 A192 192 0 0 1 352 310 L262 520 L258 360 A192 192 0 1 1 202 0 Z" fill="var(--blue)"/>
      <circle cx="202" cy="192" r="176" fill="var(--white)"/>
      <circle cx="202" cy="192" r="160" fill="url(#rocks)" role="img" aria-label="Photo of miniature excavator and workers mining gold coins among rocks"/>
    </svg>

    <p class="abs intro-band">Quillfern Vaults stands out in the industry by offering both GPU Hosting and ASIC Hosting services in our state-of-the-art facility, equipped with an impressive 17 Megawatts of available power. What sets us apart is our unique billing system based on actual metered power usage.</p>
    <p class="abs price-band">We charge $0.08 for ASIC miners and $0.09 for GPU miners, ensuring cost-effectiveness and transparency for our clients.</p>

    <h2 class="abs section-title">SOLUTIONS FOR EVERY MINER, REGARDLESS OF SCALE</h2>

    <div class="abs service grey" style="left:50px">
      <span class="service-icon"><svg width="20" height="20" viewBox="0 0 20 20" fill="none" stroke="var(--blue)" stroke-width="1.6"><rect x="3" y="7" width="14" height="8" rx="1"/><circle cx="7" cy="11" r="2"/><circle cx="13" cy="11" r="2"/><path d="M5 15v3M15 15v3M6 4h8"/></svg></span>
      <div class="service-head">GPU Hosting</div>
      <p class="service-body">Begin your GPU Hosting journey with rates starting at $0.09 kWh, accepting all equipment.</p>
    </div>
    <div class="abs service dark" style="left:238px">
      <span class="service-icon"><svg width="20" height="20" viewBox="0 0 20 20" fill="none" stroke="var(--blue)" stroke-width="1.6"><rect x="3" y="3" width="14" height="11" rx="1"/><path d="M6 7h8M6 10h5M7 17h6"/></svg></span>
      <div class="service-head">ASIC Hosting</div>
      <p class="service-body">Get your ASICs directly from us or send yours in today, starting at an all-in rate of $0.08 kWh.</p>
    </div>
    <div class="abs service grey" style="left:429px">
      <span class="service-icon"><svg width="20" height="20" viewBox="0 0 20 20" fill="none" stroke="var(--blue)" stroke-width="1.6"><rect x="5" y="5" width="10" height="10" rx="1"/><rect x="8" y="8" width="4" height="4"/><path d="M8 2v3M12 2v3M8 15v3M12 15v3M2 8h3M2 12h3M15 8h3M15 12h3"/></svg></span>
      <div class="service-head">Mining Hardware</div>
      <p class="service-body">Looking for mining hardware? Our equipment comes with no additional markup, ever.</p>
    </div>
    <div class="abs service dark" style="left:616px">
      <span class="service-icon"><svg width="20" height="20" viewBox="0 0 20 20" fill="none" stroke="var(--blue)" stroke-width="1.6"><circle cx="8" cy="8" r="5"/><circle cx="13" cy="13" r="5"/></svg></span>
      <div class="service-head">Crypto Consulting</div>
      <p class="service-body">Enjoy White Glove Services for setup, insurance, and tax consulting.</p>
    </div>

    <div class="abs commit"></div>
    <div class="abs commit-top"></div>
    <p class="abs commit-heading">Our commitment to excellence<br>is evident in our use of</p>
    <ul class="abs commit-list">
      <li><svg width="12" height="12" viewBox="0 0 12 12"><circle cx="6" cy="6" r="6" fill="var(--blue)"/><path d="M3.3 6.2l1.8 1.8 3.6-3.8" fill="none" stroke="#fff" stroke-width="1.5"/></svg>Cutting-edge technology</li>
      <li><svg width="12" height="12" viewBox="0 0 12 12"><circle cx="6" cy="6" r="6" fill="var(--blue)"/><path d="M3.3 6.2l1.8 1.8 3.6-3.8" fill="none" stroke="#fff" stroke-width="1.5"/></svg>Top-notch facilities</li>
      <li><svg width="12" height="12" viewBox="0 0 12 12"><circle cx="6" cy="6" r="6" fill="var(--blue)"/><path d="M3.3 6.2l1.8 1.8 3.6-3.8" fill="none" stroke="#fff" stroke-width="1.5"/></svg>Strategic partnerships</li>
    </ul>
    <p class="abs commit-note">These elements come together to deliver exceptional solutions tailored for real-world applications in the cryptocurrency space.</p>

    <div class="abs photo coins" role="img" aria-label="Photo of miniature miners digging around a large coin in soil"></div>
    <div class="abs photo trade" role="img" aria-label="Photo of a hand with a stylus beside a gold coin over blue city buildings"></div>

    <svg class="abs footer" width="845" height="95" viewBox="0 0 845 95">
      <polygon points="0,0 483,0 450,95 0,95" fill="var(--black)"/>
      <polygon points="472,22 486,22 462,80 448,80" fill="var(--blue)"/>
      <rect x="455" y="80" width="390" height="5" fill="var(--blue)"/>
      <rect x="450" y="85" width="395" height="10" fill="var(--black)"/>
    </svg>
    <div class="abs contact" style="left:52px">
      <svg width="15" height="15" viewBox="0 0 16 16"><path d="M3 1.5l2.6 2.8-1.4 2a9 9 0 0 0 5.5 5.5l2-1.4 2.8 2.6-1.6 2C7 14.6 1.4 9 1 3.1z" fill="var(--blue)"/></svg>012.555.0147
    </div>
    <div class="abs contact" style="left:185px">
      <svg width="16" height="12" viewBox="0 0 16 12"><rect width="16" height="12" rx="1" fill="var(--blue)"/><path d="M1 1l7 6 7-6" fill="none" stroke="var(--black)" stroke-width="1.2"/></svg>hello@quillfernvaults.example
    </div>
    <div class="abs web">
      <svg width="13" height="13" viewBox="0 0 14 14" fill="none" stroke="var(--blue)" stroke-width="1.3"><circle cx="7" cy="7" r="6"/><ellipse cx="7" cy="7" rx="2.6" ry="6"/><path d="M1 7h12"/></svg>
      <span>www.<b>quillfernvaults</b>.example</span>
    </div>
  </article>
</div>
</body>
</html>
```